Business Card & Letterhead Design

We a financial advice company based in Australia. We provide advice to wealthy farmers.

We are changing our business name FROM Brightvale Financial TO Tallowmere Wealth and we need a new letterhead and double sided business card design

Attached is designs from our previous branding (Brightvale Financial) as it includes all the details we require on the new Tallowmere Wealth business cards and letterhead.

Need extra days to review

```html
<!DOCTYPE html>
<html lang="en">
<head>
<meta charset="utf-8">
<title>Tallowmere Wealth Letterhead</title>
<link href="https://fonts.googleapis.com/css2?family=Montserrat:ital,wght@0,400;0,500;1,400&family=Mulish:wght@400&display=swap" rel="stylesheet">
<style>
  :root {
    --backdrop: #e6e7e9;
    --paper: #ffffff;
    --ink: #4a4a4c;
    --ink-soft: #5c5c60;
    --brand: #3f3f42;
    --band: #414143;
    --rule: #9a9a9d;
    --signature: #3a4fa0;
  }
  * { margin: 0; padding: 0; box-sizing: border-box; }
  html, body { width: 1200px; height: 1200px; overflow: hidden; }
  body { background: var(--backdrop); position: relative; font-family: "Mulish", sans-serif; color: var(--ink); }

  .sheet {
    position: absolute; left: 188px; top: 30px;
    width: 823px; height: 1140px;
    background: var(--paper);
    box-shadow: 0 2px 8px rgba(0,0,0,0.12);
  }

  .brand { position: absolute; left: 60px; top: 62px; width: 288px; text-align: center; }
  .brand-mark { display: block; margin: 0 auto 8px; width: 68px; height: 68px; border: 2.5px solid var(--brand); border-radius: 50%; }
  .brand-name {
    font-family: "Montserrat", sans-serif; font-weight: 400;
    font-size: 21px; letter-spacing: 1.5px; text-transform: uppercase; color: var(--brand);
  }

  .contacts { position: absolute; left: 553px; top: 67px; list-style: none; font-family: "Montserrat", sans-serif; font-size: 12px; color: var(--ink); }
  .contacts li { display: flex; align-items: center; height: 19.8px; }
  .contacts svg { width: 15px; height: 15px; margin-right: 6px; }

  .recipient { position: absolute; left: 111px; top: 246px; font-size: 12.5px; line-height: 15.3px; color: var(--ink-soft); }

  .letter-body { position: absolute; left: 73px; top: 381px; width: 676px; font-size: 12px; line-height: 15.2px; color: var(--ink-soft); }
  .letter-body p { text-align: justify; text-indent: 38px; margin-bottom: 15px; hyphens: auto; }

  .signature { position: absolute; left: 73px; top: 850px; width: 98px; height: 40px; background: linear-gradient(90deg, #dfe3f2, #eef0f8); }
  .signatory { position: absolute; left: 73px; top: 900px; font-size: 12.5px; line-height: 15.3px; color: var(--ink-soft); }

  .legal { position: absolute; left: 0; width: 100%; text-align: center; font-family: "Montserrat", sans-serif; font-size: 11px; line-height: 16.3px; color: var(--ink); }
  .legal-entity { top: 969px; }
  .legal-licensee { top: 1020px; }
  .legal-rule { position: absolute; left: 73px; top: 1012px; width: 676px; border: 0; border-top: 1px solid var(--rule); }

  .footer-band { position: absolute; left: 0; top: 1092px; width: 823px; height: 48px; }
  .footer-band svg { position: absolute; inset: 0; }
  .tagline { position: absolute; left: 0; width: 100%; top: 14px; text-align: center; font-family: "Montserrat", sans-serif; font-style: italic; font-size: 13.5px; color: #fff; }
</style>
</head>
<body>
  <article class="sheet">
    <header class="brand">
      <span class="brand-mark"></span>
      <div class="brand-name">Tallowmere Wealth</div>
    </header>

    <ul class="contacts">
      <li><svg viewBox="0 0 16 16"><circle cx="8" cy="8" r="7.2" fill="none" stroke="#4a4a4c"/><path d="M4.5 7.5c1-2 6-2 7 0l-1 1h-1v-1h-3v1h-1z" fill="#4a4a4c"/><rect x="5.5" y="8.5" width="5" height="2.5" fill="#4a4a4c"/></svg>(07) 3555 0142</li>
      <li><svg viewBox="0 0 16 16"><circle cx="8" cy="8" r="7.2" fill="none" stroke="#4a4a4c"/><rect x="5" y="4.5" width="6" height="3" fill="none" stroke="#4a4a4c"/><rect x="4" y="7" width="8" height="3.5" fill="#4a4a4c"/><rect x="5.5" y="9.5" width="5" height="2.5" fill="#fff" stroke="#4a4a4c"/></svg>(07) 3555 0187</li>
      <li><svg viewBox="0 0 16 16"><circle cx="8" cy="8" r="7.2" fill="none" stroke="#4a4a4c"/><rect x="5.8" y="3.8" width="4.4" height="8.4" rx="0.8" fill="none" stroke="#4a4a4c"/></svg>0400 555 318</li>
      <li><svg viewBox="0 0 16 16"><circle cx="8" cy="8" r="7.2" fill="none" stroke="#4a4a4c"/><rect x="4.2" y="5.5" width="7.6" height="5" fill="#4a4a4c"/><path d="M4.2 5.5l3.8 3 3.8-3" fill="none" stroke="#fff" stroke-width="0.8"/></svg>hello@tallowmerewealth.com.au</li>
      <li><svg viewBox="0 0 16 16"><circle cx="8" cy="8" r="7.2" fill="none" stroke="#4a4a4c"/><circle cx="8" cy="8" r="4" fill="none" stroke="#4a4a4c"/><path d="M4 8h8M8 4c-2 2.5-2 5.5 0 8M8 4c2 2.5 2 5.5 0 8" fill="none" stroke="#4a4a4c" stroke-width="0.7"/></svg>www.tallowmerewealth.com.au</li>
    </ul>

    <address class="recipient" style="font-style:normal">
      Mr. Daniel Mercer<br>
      Commercial Director<br>
      42 Wattle Creek Road<br>
      Dalby, QLD 4405
    </address>

    <section class="letter-body">
      <p>Lorem ipsum dolor sit amet, consectetur adipiscing elit. Suspendisse condimentum egestas tellus et viverra. Vestibulum euismod lacus eget nisi ornare, id laoreet tortor dapibus. Donec lacinia euismod diam, convallis tempus risus. Ut et felis tempor eros blandit feugiat ut non enim. In vestibulum ligula blandit magna blandit dictum. Sed malesuada erat id mauris pretium, eget congue felis interdum. Aenean ultricies enim nec lorem vestibulum, nec commodo quam sagittis. Cras bibendum, mauris eget aliquet semper, libero ipsum ultricies nunc, euismod pellentesque orci risus sit amet nibh. Maecenas feugiat mi a metus convallis pharetra.</p>
      <p>Duis porta, turpis ut pulvinar hendrerit, elit lorem vehicula turpis, lacinia semper purus eros ac nisi. Sed consectetur ante scelerisque tortor pellentesque imperdiet. Pellentesque habitant morbi tristique senectus et netus et malesuada fames ac turpis egestas. Quisque justo turpis, varius id ante nec, accumsan ultricies magna. Mauris lorem lectus, dignissim nec felis a, tincidunt pharetra tellus. Donec non euismod est. Nulla in elit quis tellus mattis feugiat vitae ut magna. Etiam at nisi quis dolor lacinia hendrerit placerat et risus. Vestibulum ac sapien ut justo varius venenatis.</p>
      <p>Donec eget nunc bibendum, sodales augue vel, dapibus nibh. Praesent mollis urna vel enim gravida aliquet nec non ipsum. Lorem ipsum dolor sit amet, consectetur adipiscing elit. Class aptent taciti sociosqu ad litora torquent per conubia nostra, per inceptos himenaeos. Phasellus et dolor ac nulla auctor consequat malesuada sit amet diam. Mauris a nunc neque. Etiam aliquet ligula in rhoncus sagittis.</p>
      <p>Sed luctus nibh erat, non varius augue vehicula ut. Nam diam est, sollicitudin in ligula vel, aliquam faucibus neque. Etiam luctus tempus ultricies. Duis posuere lobortis placerat. Suspendisse porttitor, orci eu scelerisque commodo, augue metus dictum nisl, eget facilisis mi ligula imperdiet ligula. Aenean ornare dui eu viverra ullamcorper. Etiam sed venenatis ante, id condimentum mauris. Suspendisse lobortis, ante quis suscipit pharetra, nulla ipsum malesuada mi, vitae molestie tellus velit ac sapien.</p>
    </section>

    <div class="signature" role="img" aria-label="Handwritten signature of Daniel Mercer"></div>
    <div class="signatory">Daniel Mercer<br>Commercial Director</div>

    <div class="legal legal-entity">
      Kestrel Holdings Pty Ltd - ATF The Harwood Trust - Tallowmere Wealth<br>
      ABN: 61 208 337 915 - Corporate Authorised - Representative of Meridian Advisory Partners Limited
    </div>
    <hr class="legal-rule">
    <div class="legal legal-licensee">
      Meridian Advisory Partners Limited - ABN: 48 117 620 503<br>
      Australian Financial Services Licence - Licence Number: 318 402<br>
      Principle Address: 120 Harbour Rd. P.O. Box 4410 Brisbane QLD 4000
    </div>

    <footer class="footer-band">
      <svg viewBox="0 0 823 48" width="823" height="48" aria-hidden="true">
        <rect width="823" height="48" fill="var(--band)"/>
        <polygon points="271,0 297,0 285,32" fill="#fff"/>
        <polygon points="559,0 585,0 571,32" fill="#fff"/>
      </svg>
      <div class="tagline">A Referral Built Business</div>
    </footer>
  </article>
</body>
</html>
```